Business card design needed

I would like a one sided black business card with the information provided above. Refer to my website www.brightvolleyracquets.com.au for an example of colors I have used for my site, would like to keep this consistent for my business cards also, I will upload my logo below.

I am a new small business that provides tennis customers with racquet re stringing, tennis strings and accessories.

Industry/Entity Type

Small Business

Contact Information for Business Card

Bright Volley Tennis

Owen Whitby
Managing Director

brightvolleyracquets@mailbox.example
www.brightvolleyracquets.com.au
0491 726 305

Racquet Restringing/Tennis Strings/Accessories

Requirements
Must have
• Must have my logo and card must be black

```html
<!DOCTYPE html>
<html lang="en">
<head>
<meta charset="utf-8">
<title>Bright Volley Tennis – Business Card</title>
<link rel="stylesheet" href="https://fonts.googleapis.com/css2?family=Source+Sans+3:wght@400;600;700&display=swap">
<style>
  :root {
    --page-bg: #e4e2df;
    --card-black: #050505;
    --lime: #b8d432;
    --band-blue: #2c4e86;
    --white: #ffffff;
    --text-font: "Source Sans 3", Arial, sans-serif;
  }
  * { margin: 0; padding: 0; box-sizing: border-box; }
  html, body {
    width: 1200px;
    height: 475px;
    overflow: hidden;
    background: var(--page-bg);
    font-family: var(--text-font);
  }
  .stage {
    position: relative;
    width: 1200px;
    height: 475px;
  }
  .card {
    position: absolute;
    width: 547px;
    height: 314px;
    background: var(--card-black);
    border-radius: 14px;
    overflow: hidden;
  }
  .card--front { left: 50px; top: 76px; }
  .card--back  { left: 606px; top: 84px; }

  .decor-band {
    position: absolute;
    left: 0;
    right: 0;
    top: 170px;
    bottom: 0;
    background: linear-gradient(180deg, var(--card-black) 0%, var(--band-blue) 45%, var(--band-blue) 100%);
  }

  .brand {
    position: absolute;
    display: flex;
    align-items: center;
    gap: 10px;
    color: var(--lime);
    font-weight: 700;
    font-size: 30px;
    line-height: 1;
    letter-spacing: 0.5px;
    white-space: nowrap;
  }
  .brand__dot {
    width: 22px;
    height: 22px;
    border-radius: 50%;
    background: var(--lime);
    flex: none;
  }
  .card--front .brand { left: 28px; top: 100px; }
  .card--back .brand { left: 0; right: 0; top: 128px; justify-content: center; font-size: 34px; }

  .contact-person {
    position: absolute;
    left: 368px;
    top: 98px;
  }
  .contact-person__name {
    color: var(--lime);
    font-size: 20px;
    font-weight: 400;
    letter-spacing: 0.3px;
    line-height: 1.1;
  }
  .contact-person__role {
    color: var(--lime);
    font-size: 13.5px;
    line-height: 1.4;
  }
  .contact-person__phone {
    color: var(--white);
    font-size: 21px;
    letter-spacing: 0.4px;
    margin-top: 2px;
  }

  .contact-online {
    position: absolute;
    right: 20px;
    top: 261px;
    color: var(--white);
    font-size: 14px;
    line-height: 20px;
    text-align: left;
  }

  .back-url {
    position: absolute;
    left: 0;
    right: 0;
    top: 252px;
    text-align: center;
    color: var(--white);
    font-size: 13px;
    letter-spacing: 2.2px;
  }
</style>
</head>
<body>
<main class="stage">

  <section class="card card--front" aria-label="Business card front">
    <div class="decor-band" role="img" aria-label="Decorative blue and lime wave band"></div>

    <div class="brand">
      <span class="brand__dot"></span>
      <span class="brand__name">Bright Volley Tennis</span>
    </div>

    <div class="contact-person">
      <p class="contact-person__name">OWEN WHITBY</p>
      <p class="contact-person__role">Managing Director</p>
      <p class="contact-person__phone">0491 726 305</p>
    </div>

    <div class="contact-online">
      <p>brightvolleyracquets@mailbox.example</p>
      <p>www.brightvolleyracquets.com.au</p>
    </div>
  </section>

  <section class="card card--back" aria-label="Business card back">
    <div class="brand">
      <span class="brand__dot"></span>
      <span class="brand__name">Bright Volley Tennis</span>
    </div>
    <p class="back-url">www.brightvolleyracquets.com.au</p>
  </section>

</main>
</body>
</html>
```